New Business Card for Web Design/Internet Marketing Company

Looking for a great looking new business card. We are a 10 year old web design, internet marketing and website management company that works mostly with small businesses.

Our new card needs to better match the colors and style of our website, be bold, extremely usable and slightly edgy.

Target Market(s)

Small/Medium businesses that have websites

Industry/Entity Type

Internet

Requirements
Must have
• Front and back design, full color, rounded corners please

Must use the colors/style of our website (JPG provided)

INFO FOR CARDS (as readable as possible please)
Mark Lenner
President/CEO
mark@trelvanmedia.example
Phone: 520-381-7459
Toll Free: 866-381-7459
Address: 4315 W. Calloway Ave. Ste. 140, Tucson, AZ 85792

THINGS I WANT TO PROMOTE (if there is room):
1. Our Website - www.trelvanmedia.example

2. Social Media
Twitter: @trelvanmedia
Facebook: www.facebook.com/trelvanmedia

3. Our Services
Web Design
Internet Marketing
Website Management

```html
<!DOCTYPE html>
<html lang="en">
<head>
<meta charset="utf-8">
<title>Trelvan Media – Business Card</title>
<link rel="stylesheet" href="https://fonts.googleapis.com/css2?family=Source+Sans+3:wght@400;600;700&display=swap">
<style>
  :root {
    --backdrop: #e7e4df;
    --card-white: #ffffff;
    --brand-blue: #1b95cb;
    --brand-orange: #f3892a;
    --slate: #5e5f61;
    --ink-light: #f4f4f4;
    --ink-grey: #6a6b6d;
  }
  * { box-sizing: border-box; margin: 0; padding: 0; }
  html, body { width: 1200px; height: 402px; overflow: hidden; }
  body {
    background: var(--backdrop);
    font-family: "Source Sans 3", "Helvetica Neue", Arial, sans-serif;
    position: relative;
  }
  .card {
    position: absolute;
    top: 58px;
    width: 536px;
    height: 292px;
    border-radius: 4px;
    overflow: hidden;
    box-shadow: 0 2px 6px rgba(0,0,0,.18);
  }
  .card--front { left: 61px; background: var(--card-white); }
  .card--back { left: 631px; width: 508px; background: var(--slate); }

  /* front */
  .front-wave { position: absolute; inset: 0; }
  .brand {
    position: absolute;
    top: 40px;
    left: 0; right: 0;
    display: flex;
    flex-direction: column;
    align-items: center;
  }
  .brand__row { display: flex; align-items: center; gap: 12px; }
  .brand__dot {
    width: 30px; height: 30px; border-radius: 50%;
    background: var(--brand-orange);
  }
  .brand__name {
    font-size: 44px; font-weight: 700; color: var(--brand-blue);
    letter-spacing: -0.5px; line-height: 1;
  }
  .brand__tagline {
    margin-top: 4px;
    margin-left: 150px;
    font-size: 15px; color: var(--ink-grey);
  }

  .person {
    position: absolute;
    top: 146px; left: 0; right: 0;
    text-align: center;
    color: var(--brand-blue);
  }
  .person__name { font-size: 18px; font-weight: 700; }
  .person__title { font-size: 13.5px; font-weight: 400; }

  .contact {
    position: absolute;
    top: 219px;
    font-size: 12.6px;
    line-height: 17px;
    color: var(--ink-light);
  }
  .contact--social { right: 290px; text-align: right; }
  .contact--direct { left: 275px; }
  .contact__gap { height: 3px; }
  .contact__line { display: flex; align-items: center; gap: 5px; white-space: nowrap; }
  .contact--social .contact__line { justify-content: flex-end; }
  .contact__square {
    width: 9px; height: 9px; background: var(--ink-light); border-radius: 1px;
  }
  .contact__icon { width: 10px; height: 10px; flex: none; }
  .contact__divider {
    position: absolute;
    left: 261px; top: 220px;
    width: 1px; height: 66px;
    background: var(--ink-light);
    opacity: .8;
  }

  /* back */
  .back-brand {
    position: absolute;
    top: 78px; left: 0; right: 0;
    text-align: center;
    font-size: 40px; font-weight: 700;
    color: var(--card-white);
    line-height: 1;
  }
  .services {
    position: absolute;
    top: 202px; left: 0; right: 0;
    text-align: center;
    font-size: 18.5px;
    line-height: 27px;
    color: var(--card-white);
  }
  .services__sep { margin: 0 6px; }
</style>
</head>
<body>

<section class="card card--front" aria-label="Card front">
  <svg class="front-wave" viewBox="0 0 536 292" width="536" height="292" aria-hidden="true">
    <path d="M0 236 Q268 140 536 236 L536 292 L0 292 Z" fill="var(--brand-orange)"/>
    <path d="M0 244 Q268 156 536 244 L536 292 L0 292 Z" fill="var(--slate)"/>
  </svg>

  <header class="brand">
    <div class="brand__row">
      <span class="brand__dot"></span>
      <span class="brand__name">Trelvan Media</span>
    </div>
    <p class="brand__tagline">Grow your Presence</p>
  </header>

  <p class="person"><span class="person__name">Mark Lenner,</span> <span class="person__title">President/CEO</span></p>

  <div class="contact contact--social">
    <p class="contact__line"><span class="contact__square"></span>trelvanmedia</p>
    <p class="contact__line"><span class="contact__square"></span>@trelvanmedia</p>
    <div class="contact__gap"></div>
    <p class="contact__line">4315 W. Calloway Ave. Ste. 140</p>
    <p class="contact__line">Tucson, AZ 85792</p>
  </div>

  <span class="contact__divider"></span>

  <div class="contact contact--direct">
    <p class="contact__line">
      <svg class="contact__icon" viewBox="0 0 10 10"><circle cx="5" cy="5" r="4.3" fill="none" stroke="currentColor" stroke-width="1"/><path d="M3.3 2.8 L4.3 2.8 L4.6 4 L4 4.5 Q4.6 5.7 5.6 6.1 L6.1 5.5 L7.2 5.8 L7.2 6.8 Q4.5 7 3.3 2.8 Z" fill="currentColor"/></svg>
      520-381-7459
    </p>
    <p class="contact__line">
      <svg class="contact__icon" viewBox="0 0 10 10"><path d="M2 1.5 L3.8 1.5 L4.3 3.6 L3.3 4.4 Q4.3 6.2 5.8 6.9 L6.6 5.9 L8.5 6.4 L8.5 8.3 Q3 8.5 2 1.5 Z" fill="currentColor"/></svg>
      866-381-7459
    </p>
    <div class="contact__gap"></div>
    <p class="contact__line">
      <svg class="contact__icon" viewBox="0 0 10 10"><rect x="0.8" y="2.2" width="8.4" height="5.8" fill="currentColor"/><path d="M0.8 2.2 L5 5.4 L9.2 2.2" fill="none" stroke="var(--slate)" stroke-width="0.9"/></svg>
      mark@trelvanmedia.example
    </p>
    <p class="contact__line">
      <svg class="contact__icon" viewBox="0 0 10 10" fill="none" stroke="currentColor" stroke-width="0.9"><circle cx="5" cy="5" r="4.2"/><ellipse cx="5" cy="5" rx="1.8" ry="4.2"/><path d="M0.8 5 H9.2"/></svg>
      www.trelvanmedia.example
    </p>
  </div>
</section>

<section class="card card--back" aria-label="Card back">
  <p class="back-brand">Trelvan Media</p>
  <div class="services">
    <p>Web Design<span class="services__sep">•</span>Internet Marketing</p>
    <p>Website Management</p>
  </div>
</section>

</body>
</html>
```